Small legal and financial translation company needs Squarespace website, brochure and logo

Hello,
We are Lumarin Services (www.lumarinservices-example.com), a boutique legal and financial translation company. We offer our services mainly to Spanish customers. Our primary line of business is the translation of financial statements, but we translate a wide variety legal and financial texts.
The project we are offering comprises three parts: a redo of the current website, an informational brochure for potential customer and a logo design. These three parts should provide a consistent image. We would develop content soon.
We are looking for a website that would look like a typical law firm website, nothing too fancy. Right now, it is in English, Spanish and French, although the new site need only be in English and Spanish. There must be good toggling between the English and Spanish versions. There would be no need for tie-ins to social media and it would not contain a blog. Basically, a static site. We aren't interesting in driving traffic to the site or SEO, as we will contact nearly all potential customers beforehand. The website must be built in Squarespace to enable a smooth transition. The content would be similar to the current page, we'll be working on the exact content, but a rough draft is attached.
The brochure will be some three pages and would introduce the company to potential customers, using similar images as the website and the logo to be designed.
The only specifications for the logo is, as the website and brochure, it convey a sense of security and trust.
Feel free to ask with any questions as this is the first time we have used this platform.
Thank you!
Updates

I've added a more or less final version for the text in the brochure and updated the brief. Added Wednesday, June 10, 2015

Target Market(s)

Spanish law firms, auditors, accountants, banks, investment firms

Industry/Entity Type

Finance

Logo Text

Lumarin Services

Number of Pages Required

5+ page

Font styles to use
Serif

Requirements
Must have
• The website must be built in Squarespace and have a good option to toggle between English and Spanish versions.
• Brochure must be in both English and Spanish, I'm attaching a rough draft of the information that it will probably have. This should give an idea about what to include and the spacing. I will update it to include the final information.
Nice to have
• Would be nice to have some quality finance- and legal-related images
Should not have
• Vibrant colours

```html
<!DOCTYPE html>
<html lang="en">
<head>
<meta charset="utf-8">
<title>Lumarin Services – Brochure</title>
<link rel="stylesheet" href="https://fonts.googleapis.com/css2?family=Crimson+Text:wght@400;600&family=Oswald:wght@500&display=swap">
<style>
:root{
  --board:#bfbfbf;
  --ink:#111;
  --paper:#fff;
  --black:#0c0c0c;
  --soft:#e6e6e6;
  --row:#dcdcdc;
  --muted:#cfcfcf;
  --text:#333;
}
*{box-sizing:border-box;margin:0;padding:0}
html,body{width:713px;height:1200px;overflow:hidden;background:var(--board)}
body{position:relative;font-family:"Crimson Text",Georgia,serif;color:var(--text)}
.sheet-label{position:absolute;left:0;width:713px;text-align:center;font-family:"Oswald",Arial,sans-serif;font-weight:500;font-size:15px;color:var(--ink);letter-spacing:.3px}
.sheet{position:absolute;left:27px;width:653px;height:504px;background:var(--paper);box-shadow:0 2px 8px rgba(0,0,0,.35);overflow:hidden}
.sheet--outside{top:88px}
.sheet--inside{top:668px}
.panel{position:absolute;top:0;height:504px}
.panel--left{left:0;width:218px}
.panel--mid{left:218px;width:216px;background:var(--black);color:#eee}
.panel--right{left:434px;width:219px}
.photo{position:absolute}
.photo--team{left:0;top:0;width:218px;height:192px;background:linear-gradient(160deg,#8a8a8a,#3a3a3a 55%,#bdbdbd)}
.photo--justice{left:0;top:79px;width:219px;height:283px;background:linear-gradient(135deg,#d9d9d9,#8c8c8c 50%,#cfcfcf)}
.photo--gavel{left:0;top:330px;width:218px;height:174px;background:linear-gradient(180deg,rgba(255,255,255,0),#9a9a9a 70%,#6d6d6d)}
.photo--signing{left:0;top:334px;width:219px;height:170px;background:linear-gradient(160deg,#f0f0f0,#9c9c9c 60%,#d4d4d4)}
.panel--mid.textured{background:linear-gradient(160deg,#1c1c1c,#050505 60%,#141414)}
.heading{font-weight:400;color:var(--ink);font-size:15px}
.body-text{font-size:7.3px;line-height:9.6px;text-align:justify;color:#444}
.about{position:absolute;left:10px;width:198px}
.about--who{top:202px}
.about--what{top:344px}
.about .heading{margin-bottom:9px}
.why-title{position:absolute;top:22px;width:100%;text-align:center;font-size:16px;color:#fff}
.benefits{position:absolute;top:58px;width:100%;list-style:none;text-align:center}
.benefit{font-size:8px;line-height:10px;color:#eee;margin-bottom:15px}
.benefit svg{display:block;margin:0 auto 3px}
.contact{position:absolute;top:374px;width:100%;text-align:center}
.contact-title{font-size:16px;color:#fff;margin-bottom:16px}
.contact p{font-size:8px;color:#eee;margin-bottom:10px}
.brand{position:absolute;top:0;left:0;width:219px;height:70px;display:flex;align-items:center;justify-content:center;font-size:21px;letter-spacing:1.5px;color:var(--ink)}
.brand-bar{position:absolute;top:70px;left:0;width:219px;height:9px;background:var(--black)}
.tagline{position:absolute;top:362px;left:0;width:219px;height:90px;background:var(--black);color:#fff;font-size:13.2px;line-height:17px;text-align:center;padding-top:16px}
.site{position:absolute;top:464px;width:219px;text-align:center;font-size:10.5px;color:var(--ink)}
.expertise-title{position:absolute;left:11px;top:18px;font-size:15px;color:var(--ink)}
.expertise-list{position:absolute;left:10px;top:52px;width:200px;list-style:none}
.expertise{position:relative;padding-left:40px;height:90px}
.num{position:absolute;left:0;top:6px;width:26px;height:26px;border:1px solid var(--ink);border-radius:50%;text-align:center;line-height:24px;font-size:15px;color:var(--ink);background:rgba(255,255,255,.6)}
.expertise h3{font-size:8.4px;font-weight:600;color:var(--ink);margin-bottom:2px}
.diff-title{position:absolute;left:16px;top:16px;width:190px;font-size:14.5px;line-height:19px;color:#fff;font-weight:400}
.diff-body{position:absolute;left:11px;width:196px;color:#ccc}
.diff-body--a{top:92px}
.diff-body--b{top:314px}
.diff-body--c{top:381px}
.diff-list{position:absolute;left:11px;top:156px;list-style:none}
.diff-list li{font-size:7.3px;color:#ccc;margin-bottom:10.5px}
.diff-list li::before{content:"•";margin-right:3px}
.pricing-title{position:absolute;left:11px;top:16px;font-size:15px;color:var(--ink)}
.price-table{position:absolute;left:9px;top:44px;width:201px;border-collapse:collapse;font-size:7.4px}
.price-table th{background:var(--black);color:#fff;font-weight:600;font-size:8.4px;height:30px;text-align:left;padding-left:9px}
.price-table th.amount,.price-table td.amount{text-align:center;width:66px;padding-left:0}
.price-table td{height:26px;padding-left:9px;color:#444;background:var(--soft);border-bottom:1px solid #fff}
.price-table tr:nth-child(even) td{background:var(--row)}
</style>
</head>
<body>
<h2 class="sheet-label" style="top:38px">BROCHURE OUTSIDE</h2>
<section class="sheet sheet--outside">
  <div class="panel panel--left">
    <div class="photo photo--team" role="img" aria-label="Photo of a team of business professionals in suits"></div>
    <div class="about about--who">
      <h3 class="heading">Who Are We?</h3>
      <p class="body-text">We are a small, highly professional and qualified group of professionals with backgrounds in law, financial services and translation and interpretation that boasts experience in global consulting and auditing firms, law firms and companies from a cross section of industries. Sensitive to the workings of the financial world, we are detail-oriented experts striving to facilitate understanding among investors, companies and international organisations.</p>
    </div>
    <div class="about about--what">
      <h3 class="heading">What We Do?</h3>
      <p class="body-text">We provide high-quality translation services in English, Spanish and French for legal and financial documents, particularly for your company's financial statements and annual reports. The translation tools we have fashioned over the years ensure that your investors and other parties recognise your company's worth and dedication while reflecting the distinction between financial statements prepared under IFRSs or local GAAP. We foster long-term relationships with our clients to develop a consistent image across varied translations and follow strict standards to maintain that consistency over time.</p>
    </div>
  </div>
  <div class="panel panel--mid textured">
    <h3 class="why-title">Why Choose Us?</h3>
    <ul class="benefits">
      <li class="benefit"><svg width="18" height="16" viewBox="0 0 18 16"><ellipse cx="9" cy="9" rx="7" ry="5.5" fill="#fff"/><rect x="5" y="13" width="2" height="3" fill="#fff"/><rect x="11" y="13" width="2" height="3" fill="#fff"/><rect x="7.5" y="1" width="3" height="2" fill="#fff"/></svg>Save money</li>
      <li class="benefit"><svg width="18" height="17" viewBox="0 0 18 17"><polygon points="9,0 11.6,6 18,6.4 13,10.6 14.6,17 9,13.5 3.4,17 5,10.6 0,6.4 6.4,6" fill="#fff"/></svg>Quality Guaranteed</li>
      <li class="benefit"><svg width="20" height="18" viewBox="0 0 20 18"><circle cx="7" cy="6" r="3.5" fill="#fff"/><path d="M1 18c0-5 3-7 6-7s6 2 6 7z" fill="#fff"/><rect x="12" y="0" width="7" height="5" rx="1" fill="none" stroke="#fff"/></svg>Native Translators Only</li>
      <li class="benefit"><svg width="16" height="16" viewBox="0 0 16 16"><circle cx="8" cy="8" r="6.5" fill="none" stroke="#fff" stroke-width="2"/><path d="M8 4v4h3" stroke="#fff" stroke-width="1.6" fill="none"/></svg>Consistency Over Time<br>(develop the customer's own voice in another language)</li>
      <li class="benefit"><svg width="18" height="14" viewBox="0 0 18 14"><rect x="2" y="1" width="14" height="9" fill="none" stroke="#fff" stroke-width="1.6"/><rect x="0" y="11" width="18" height="2" fill="#fff"/></svg>Use of Technology Helps Cut Costs</li>
    </ul>
    <div class="contact">
      <h3 class="contact-title">Contact Us</h3>
      <p>218 Harbor Lane Westbrook, FL 30000</p>
      <p>(555) 013-2480</p>
      <p>info@lumarinservices-example.com</p>
      <p>www.lumarinservices-example.com</p>
    </div>
  </div>
  <div class="panel panel--right">
    <h1 class="brand">LUMARIN SERVICES</h1>
    <div class="brand-bar"></div>
    <div class="photo photo--justice" role="img" aria-label="Photo of a Lady Justice statuette on a desk beside a person writing"></div>
    <p class="tagline">High-quality translation services<br>in English, Spanish and French<br>for legal and financial documents</p>
    <p class="site">www.lumarinservices-example.com</p>
  </div>
</section>

<h2 class="sheet-label" style="top:622px">BROCHURE INSIDE</h2>
<section class="sheet sheet--inside">
  <div class="panel panel--left">
    <div class="photo photo--gavel" role="img" aria-label="Faded photo of a judge's gavel and scales on a law book"></div>
    <h3 class="expertise-title">Areas of Expertise</h3>
    <ol class="expertise-list">
      <li class="expertise"><span class="num">1</span><h3>Duis autem vel eum iriure dolor</h3><p class="body-text">Lorem ipsum dolor sit amet, consectetuer adipiscing elit, sed diam nonummy nibh euismod tincidunt ut laoreet dolore magna aliquam erat volutpat. Ut wisi enim ad minim veniam, quis nostrud exerci tation ullamcorper suscipit lobortis nisl ut aliquip ex ea commodo consequat.</p></li>
      <li class="expertise"><span class="num">2</span><h3>Duis autem vel eum iriure dolor</h3><p class="body-text">Lorem ipsum dolor sit amet, consectetuer adipiscing elit, sed diam nonummy nibh euismod tincidunt ut laoreet dolore magna aliquam erat volutpat. Ut wisi enim ad minim veniam, quis nostrud exerci tation ullamcorper suscipit lobortis nisl ut aliquip ex ea commodo consequat.</p></li>
      <li class="expertise"><span class="num">3</span><h3>Duis autem vel eum iriure dolor</h3><p class="body-text">Lorem ipsum dolor sit amet, consectetuer adipiscing elit, sed diam nonummy nibh euismod tincidunt ut laoreet dolore magna aliquam erat volutpat. Ut wisi enim ad minim veniam, quis nostrud exerci tation ullamcorper suscipit lobortis nisl ut aliquip ex ea commodo consequat.</p></li>
      <li class="expertise"><span class="num">4</span><h3>Duis autem vel eum iriure dolor</h3><p class="body-text">Lorem ipsum dolor sit amet, consectetuer adipiscing elit, sed diam nonummy nibh euismod tincidunt ut laoreet dolore magna aliquam erat volutpat. Ut wisi enim ad minim veniam, quis nostrud exerci tation ullamcorper suscipit lobortis nisl ut aliquip ex ea commodo consequat.</p></li>
    </ol>
  </div>
  <div class="panel panel--mid">
    <h3 class="diff-title">Differences between working with a translation agency and a translation provider</h3>
    <p class="body-text diff-body diff-body--a">Lorem ipsum dolor sit amet, consectetuer adipiscing elit, sed diam nonummy nibh euismod tincidunt ut laoreet dolore magna aliquam erat volutpat. Ut wisi enim ad minim veniam, quis nostrud exerci tation ullamcorper suscipit lobortis nisl ut aliquip ex ea commodo consequat.</p>
    <ul class="diff-list">
      <li>Nam liber tempor cum soluta nobis</li>
      <li>Eleifend option congue nihil imperdiet doming</li>
      <li>Id quod mazim placerat facer possim assum</li>
      <li>Typi non habent claritatem insitam; est usus</li>
      <li>Legentis in iis qui facit eorum claritatem.</li>
      <li>Investigationes demonstraverunt lectores</li>
      <li>Legere me lius quod ii legunt saepius.</li>
    </ul>
    <p class="body-text diff-body diff-body--b">Duis autem vel eum iriure dolor in hendrerit in vulputate velit esse molestie consequat, vel illum dolore eu feugiat nulla facilisis at vero eros et accumsan et iusto odio dignissim qui blandit praesent luptatum zzril delenit augue duis dolore te feugait nulla facilisi. Nam liber tempor cum soluta nobis eleifend option congue nihil imperdiet doming id quod mazim placerat facer possim assum.</p>
    <p class="body-text diff-body diff-body--c">Typi non habent claritatem insitam; est usus legentis in iis qui facit eorum claritatem. Investigationes demonstraverunt lectores legere me lius quod ii legunt saepius. Claritas est etiam processus dynamicus, qui sequitur mutationem consuetudium lectorum. Mirum est notare quam littera gothica, quam nunc putamus parum claram, anteposuerit litterarum formas humanitatis per seacula quarta decima et quinta decima. Eodem modo typi, qui nunc nobis videntur parum clari, fiant sollemnes in futurum.</p>
  </div>
  <div class="panel panel--right">
    <h3 class="pricing-title">Pricing</h3>
    <table class="price-table">
      <thead><tr><th>Description</th><th class="amount">Amount</th></tr></thead>
      <tbody>
        <tr><td>Lorem ipsum dolor sit amet</td><td class="amount">$100</td></tr>
        <tr><td>Consectetuer adipiscing elit</td><td class="amount">$100</td></tr>
        <tr><td>Sed diam nonummy nibh</td><td class="amount">$100</td></tr>
        <tr><td>Euismod tincidunt ut laoreet dolore</td><td class="amount">$100</td></tr>
        <tr><td>Magna aliquam erat volutpat</td><td class="amount">$100</td></tr>
        <tr><td>Ut wisi enim ad minim veniam</td><td class="amount">$100</td></tr>
        <tr><td>Quis nostrud exerci tation</td><td class="amount">$100</td></tr>
        <tr><td>Ullamcorper suscipit lobortis</td><td class="amount">$100</td></tr>
        <tr><td>Nisl ut aliquip ex ea</td><td class="amount">$100</td></tr>
        <tr><td>Commodo consequat.</td><td class="amount">$100</td></tr>
      </tbody>
    </table>
    <div class="photo photo--signing" role="img" aria-label="Photo of a hand signing a document with a pen"></div>
  </div>
</section>
</body>
</html>
```